Fitness Equipment & Service

I want to make the card eye catching and fun. We are called Corvane Motion Limited and we are based in Wales. We sell, install and service all types of fitness equipment from Skipping ropes, right through the Dumbbells, Kettle bells and Barbells through to state of the art Treadmills, Running Machines and Strength Equipment. We also design and install changing room furniture and lockers.

TYPOGRAPHY
We would like to use Futrura. Futura has an appearance of efficiency and forwardness. The typeface is derived
from simple geometric forms (near-perfect circles, triangles and squares) and is based on strokes of
near-even weight, which are low in contrast. This is most visible in the almost perfectly round stroke of
the o, which is nonetheless slightly ovoid.
The lowercase has tall ascenders, which rise above the cap line. The uppercase
characters present proportions similar to those of classical Roman capitals.

TYPOGRAPHIC CONSIDERATIONS
No Strike though
No Horizontal Scaling
No Drop Shadows
No Effects
Never use less than 120% Leading

OUR CORPORATE COLOURS
BRAND GUIDELINES
We were thinking that our primary colour palette consists of the Acid Green (Pantone 382) and Process Black.

We work closely with tquarly Ltd and would like to include their name on the card somewhere. I have attached images of the other brands that we work with as an idea or the small icons I have included that illustrate what we do?. I have very kindly been given permission to use any of the images off the files that I have included below, so I hope these help. I will include these below. I would be open to suggestions if it made the card more striking Can you do it?
Updates

Hi All, Just wanted to add a few thoughts but you are the guys with the creative visions (thats why are here) We are based in Wales, UK and we would be open to lots of different ideas on a theme but must be eye catching, Bold and FUN. If you can or think that the Welsh or any dragon could be put in there then go for it (its not a must have) We have also added some ideas for colour but again its over to you!! GO FOR IT ! Thanks and look forward to your visions! Owen

Hi All, Just thought I would sen through the contact details that need to be on the card. (if you want to play around with icons instead of the wording twitter, Facebook, go for it): Corvane Motion Limited Owen Pritchard Managing Director Mob: +44 (0)7582 913 406 e-mail: sales@corvanemotion.co.uk Web: Corvanemotion.co.uk twitter: @motionLetterbin Facebook: Corvane Motion Limited

```html
<!DOCTYPE html>
<html lang="en">
<head>
<meta charset="utf-8">
<title>Corvane Motion Limited – Business Card</title>
<link href="https://fonts.googleapis.com/css2?family=Arimo:wght@400;700&display=swap" rel="stylesheet">
<style>
  :root {
    --navy: #14286b;
    --navy-deep: #0d1c4f;
    --navy-light: #2a4a9a;
    --gold: #b08a3a;
    --gold-light: #d8b869;
    --ink: #3d3f45;
    --rule: #d4d6dc;
    --paper: #ffffff;
    --stage: #e9eaee;
  }
  * { margin: 0; padding: 0; box-sizing: border-box; }
  html, body {
    width: 1200px; height: 950px; overflow: hidden;
    background: var(--stage);
    font-family: "Arimo", Arial, sans-serif;
  }
  .card {
    position: absolute; left: 250px;
    width: 700px; height: 400px;
    overflow: hidden;
    box-shadow: 0 6px 18px rgba(0,0,0,.18);
  }

  /* ---------- back of card ---------- */
  .card-back {
    top: 40px;
    background: linear-gradient(100deg, var(--navy-deep) 0%, var(--navy-light) 55%, var(--navy) 80%, var(--navy-deep) 100%);
  }
  .back-name {
    position: absolute; left: 0; right: 0; top: 160px;
    text-align: center;
    color: var(--paper);
    font-weight: 700; font-size: 36px; line-height: 1.2;
    letter-spacing: .5px;
  }
  .back-web {
    position: absolute; right: 40px; bottom: 44px;
    display: flex; align-items: center; gap: 12px;
    color: var(--paper); font-size: 17px; letter-spacing: 1px;
  }
  .back-web::after {
    content: ""; width: 90px; height: 1px; background: rgba(255,255,255,.7);
  }

  /* ---------- front of card ---------- */
  .card-front { top: 510px; background: var(--paper); }
  .brand {
    position: absolute; left: 40px; top: 70px; width: 260px;
    display: flex; flex-direction: column; align-items: center; gap: 18px;
  }
  .brand-mark {
    width: 110px; height: 110px; border-radius: 50%;
    background: var(--navy);
  }
  .brand-name {
    color: var(--navy); font-weight: 700; font-size: 24px; line-height: 1.2;
    text-align: center;
  }
  .divider {
    position: absolute; left: 325px; top: 80px;
    width: 1px; height: 200px; background: var(--rule);
  }
  .contact {
    position: absolute; left: 350px; top: 78px; right: 20px;
    color: var(--ink); font-size: 16px; line-height: 1.25;
  }
  .contact-name { color: var(--navy); font-weight: 700; font-size: 23px; }
  .contact-role { color: var(--gold); font-size: 17px; margin-bottom: 8px; }
  .contact-address { margin-bottom: 6px; }
  .contact-list { list-style: none; }
  .contact-list li { display: flex; align-items: center; gap: 9px; }
  .contact-list svg { width: 14px; height: 14px; flex: none; }

  .web-band {
    position: absolute; left: 0; top: 300px;
    width: 560px; height: 36px;
    background: linear-gradient(90deg, var(--navy) 0%, var(--navy-light) 100%);
    color: var(--paper); font-size: 18px; letter-spacing: 1px;
    padding-left: 40px; line-height: 36px;
  }
  .accent-band {
    position: absolute; left: 480px; top: 340px;
    width: 220px; height: 26px;
    background: linear-gradient(90deg, var(--gold) 0%, var(--gold-light) 60%, var(--gold) 100%);
  }
  .band-dot {
    position: absolute; left: 505px; top: 308px;
    width: 54px; height: 54px; border-radius: 50%;
    background: var(--navy); border: 3px solid var(--paper);
  }
</style>
</head>
<body>

<section class="card card-back" aria-label="Card back">
  <p class="back-name">Corvane Motion Limited</p>
  <p class="back-web">corvanemotion.co.uk</p>
</section>

<section class="card card-front" aria-label="Card front">
  <div class="brand">
    <span class="brand-mark"></span>
    <p class="brand-name">Corvane Motion Limited</p>
  </div>

  <span class="divider"></span>

  <div class="contact">
    <p class="contact-name">Owen Pritchard</p>
    <p class="contact-role">Managing Director</p>
    <p class="contact-address">27 Harbour Row<br>Penlan Quay, CF10 4RT</p>
    <ul class="contact-list">
      <li>
        <svg viewBox="0 0 14 14" aria-hidden="true"><rect x="3" y="0.5" width="8" height="13" rx="1.5" fill="none" stroke="#14286b" stroke-width="1.5"/><circle cx="7" cy="11" r="0.9" fill="#14286b"/></svg>
        +44 (0)7582 913 406
      </li>
      <li>
        <svg viewBox="0 0 14 14" aria-hidden="true"><rect x="0.5" y="2.5" width="13" height="9" fill="#14286b"/><path d="M0.5 2.5 L7 8 L13.5 2.5" fill="none" stroke="#fff" stroke-width="1.2"/></svg>
        sales@corvanemotion.co.uk
      </li>
      <li>
        <svg viewBox="0 0 14 14" aria-hidden="true"><rect x="1" y="1" width="12" height="12" rx="2" fill="#14286b"/></svg>
        @motionLetterbin
      </li>
      <li>
        <svg viewBox="0 0 14 14" aria-hidden="true"><rect x="1" y="1" width="12" height="12" rx="2" fill="#14286b"/></svg>
        Corvane Motion Limited
      </li>
    </ul>
  </div>

  <div class="web-band">Corvanemotion.co.uk</div>
  <span class="accent-band"></span>
  <span class="band-dot"></span>
</section>

</body>
</html>
```